Brightline Energy Product Distribution Brochure

We are looking to have our current brochure for our customers completely redesigned...the idea is to present the relevant information in an attractive way . Our website is brightlineenergyco.example where you can find more information about us. We have included a file with a rough idea of the page order and what each should include but feel free to adapt based on design. The example provided is only for context and doesnt have to be maintained. We will be using the brochure both digitally and in print form. As long as it reads easily and is eye catching, the design can be horizontal or vertical.Final deliverable should be indesign file.

"Our Brands" page: should be limited to one page (space being enough) where it has the header for each one (for example diesel generators) space for one or two lines of text and then the corresponding logos for each of the five categories
Updates

For those asking: the "our brands" page should be a single page layout where there is a header with the corresponding section and space for maybe one line of text followed by the two logos for that category. Each of the product pages should be similar in fashion to the one in the document attached: a photo of the product with some white space and space for the text to be included. We will be posting additional examples today

Target Market(s)

We want to present it to customers both digitally and in print so they can see our products

Industry/Entity Type

Power Generation

Font styles to use
Serif

Requirements
Must have
• Eye catching and able to present the information in a presentable fashion. Rest is up to you.
Nice to have
• Should incorporate the colors of our logo but can also add other depending on design

```html
<!DOCTYPE html>
<html lang="en">
<head>
<meta charset="utf-8">
<title>Brightline Energy – Product Brochure Spreads</title>
<link href="https://fonts.googleapis.com/css2?family=Archivo+Black&family=Montserrat:wght@400;500;600;700&display=swap" rel="stylesheet">
<style>
  :root{
    --navy:#1c2542;
    --ink:#2f2f33;
    --body:#4a4a4e;
    --yellow:#f7c600;
    --orange:#f08a1c;
    --grey-bg:#c5c6c8;
    --grey-band:#8e8f92;
    --white:#ffffff;
  }
  *{box-sizing:border-box;margin:0;padding:0}
  html,body{width:1200px;height:1200px;overflow:hidden}
  body{background:var(--grey-bg);font-family:"Montserrat",sans-serif;position:relative}
  .band{position:absolute;left:0;width:1200px;background:var(--grey-band)}
  .spread{position:absolute;width:518px;height:334px;box-shadow:0 3px 8px rgba(0,0,0,.35);background:var(--white)}
  .page{position:absolute;top:0;width:259px;height:334px;overflow:hidden;background:var(--white)}
  .page.left{left:0}
  .page.right{left:259px;border-left:1px solid #e3e3e3}
  .bg{position:absolute;inset:0;width:259px;height:334px}
  .chevron{position:absolute;left:0;top:0;width:518px;height:334px;z-index:2;pointer-events:none}
  .abs{position:absolute;z-index:1}
  .page-num{position:absolute;z-index:3;bottom:4px;left:12px;width:32px;height:14px;background:var(--yellow);font:11px/14px "Archivo Black",sans-serif;color:var(--ink);text-align:center}
  .baseline{position:absolute;z-index:2;bottom:4px;left:44px;right:0;height:2px;background:var(--ink)}
  .kicker{font:600 9px/1 "Montserrat",sans-serif;color:var(--white);letter-spacing:.4px}
  .title{font:17.5px/1 "Archivo Black",sans-serif;color:var(--yellow);letter-spacing:.2px;white-space:nowrap}
  .title.rule{padding-bottom:5px;border-bottom:2px solid var(--yellow)}
  .sub{font:600 8px/1.3 "Montserrat",sans-serif;color:var(--white);letter-spacing:.3px}
  .label{font:500 6.5px/1 "Montserrat",sans-serif;color:var(--orange);letter-spacing:.3px}
  .tiny{font:400 4px/1.38 "Montserrat",sans-serif;color:var(--body)}
  .tiny p+p{margin-top:3px}
  ul.tiny{list-style:none}
  ul.tiny li{padding-left:6px;position:relative}
  ul.tiny li::before{content:"";position:absolute;left:0;top:1.6px;width:2.2px;height:2.2px;background:var(--orange)}
  ul.tiny b{color:var(--orange);font-weight:700}
  .spaced li+li{margin-top:6px}
  .photo{position:absolute;z-index:1}
  .ph-night{background:radial-gradient(ellipse at 70% 85%,rgba(245,170,60,.75),transparent 55%),radial-gradient(ellipse at 20% 70%,rgba(230,140,40,.45),transparent 50%),linear-gradient(160deg,#1a2342,#2b3350 55%,#4a3a2a)}
  .ph-office{background:radial-gradient(ellipse at 30% 40%,rgba(140,170,220,.55),transparent 55%),linear-gradient(170deg,#56607c,#232a40 70%,#171b28)}
  .ph-warehouse{background:radial-gradient(ellipse at 65% 35%,rgba(60,70,110,.7),transparent 35%),linear-gradient(120deg,#d6b27a,#a9783f 55%,#6b4c2c)}
  .ph-panel{background:radial-gradient(ellipse at 50% 20%,rgba(120,170,160,.55),transparent 30%),linear-gradient(90deg,#2a2c33,#44464f 50%,#24262c)}
  .ph-genset{background:linear-gradient(90deg,#1e1e1e 0 14%,transparent 14%),linear-gradient(#fbfbfb 0%,#e4e4e4 80%,#151515 80%,#151515 100%)}
  .ph-machine{background:radial-gradient(circle at 45% 45%,#5a5a5c,#262628 45%,#0e0e0e 75%)}
  .ph-board{background:radial-gradient(ellipse at 40% 40%,#4b6bb3,#1f3270 70%)}
  .ph-module{background:linear-gradient(160deg,#fafafa,#d4d4d4 70%,#b7b7b7)}
  .ph-controller{background:radial-gradient(ellipse at 55% 28%,#5fbf6e 0 14%,transparent 15%),linear-gradient(#2d2d2f,#0c0c0d);border-radius:6px}
  .ph-cabinet{background:linear-gradient(90deg,#f3f3f3,#d9d9d9 70%,#bfbfbf)}
  .genset-kw{position:absolute;top:6px;right:5px;font:700 5.5px "Montserrat",sans-serif;color:#222}
  /* index */
  .index-title{font:18px/1 "Archivo Black",sans-serif;color:var(--ink)}
  .index-list{list-style:none;width:94px}
  .index-list li{display:flex;align-items:center;font:700 4.2px/1 "Montserrat",sans-serif;color:var(--ink);height:10px}
  .index-list li.sub-item{font-weight:400;padding-left:13px}
  .index-list li.sub-item::before{content:"";width:2.2px;height:2.2px;background:var(--orange);margin-right:3px}
  .index-list .dots{flex:1;height:1px;background:var(--yellow);margin:0 3px}
  .index-list .num{font:8.5px/1 "Archivo Black",sans-serif;color:var(--yellow);width:11px;text-align:right}
  /* brands */
  .brand-row{position:absolute;z-index:1;left:26px;width:210px;height:42px}
  .brand-row .tiny{width:112px;margin-top:4px}
  .brand-names{position:absolute;left:124px;top:6px;width:86px;display:flex;justify-content:space-between;align-items:center}
  .brand-name{font:700 6.5px/1.15 "Montserrat",sans-serif;color:var(--navy);text-align:center}
  .note-box{background:var(--yellow);font:700 5.2px/1.35 "Montserrat",sans-serif;color:var(--navy);padding:7px 8px}
  .dist-strip{background:var(--white);display:flex;justify-content:space-around;align-items:center;padding:0 4px}
  .dist-strip span{font:700 5px/1 "Montserrat",sans-serif;color:var(--navy)}
  .pname{font:600 9px/1.15 "Montserrat",sans-serif;color:var(--orange)}
</style>
</head>
<body>

<svg width="0" height="0" style="position:absolute" aria-hidden="true">
  <defs>
    <linearGradient id="g-night" x1="0" y1="0" x2="1" y2="1">
      <stop offset="0" stop-color="#19213f"/>
      <stop offset=".55" stop-color="#2b3250"/>
      <stop offset="1" stop-color="#4b3b28"/>
    </linearGradient>
    <radialGradient id="g-glow" cx=".72" cy=".85" r=".55">
      <stop offset="0" stop-color="#f6aa3c" stop-opacity=".85"/>
      <stop offset="1" stop-color="#f6aa3c" stop-opacity="0"/>
    </radialGradient>
    <radialGradient id="g-glow2" cx=".2" cy=".7" r=".45">
      <stop offset="0" stop-color="#e88a2a" stop-opacity=".55"/>
      <stop offset="1" stop-color="#e88a2a" stop-opacity="0"/>
    </radialGradient>
    <linearGradient id="g-plant" x1="0" y1="0" x2="0" y2="1">
      <stop offset="0" stop-color="#3a4466"/>
      <stop offset=".45" stop-color="#8a6a3c"/>
      <stop offset=".7" stop-color="#d89a3a"/>
      <stop offset="1" stop-color="#5b3c1a"/>
    </linearGradient>
    <linearGradient id="g-sky" x1="0" y1="0" x2="0" y2="1">
      <stop offset="0" stop-color="#202a48"/>
      <stop offset=".55" stop-color="#a47233"/>
      <stop offset="1" stop-color="#3b2b1c"/>
    </linearGradient>
    <linearGradient id="g-steel" x1="0" y1="0" x2="1" y2="1">
      <stop offset="0" stop-color="#8f8f94"/>
      <stop offset=".5" stop-color="#4a4c55"/>
      <stop offset="1" stop-color="#23283a"/>
    </linearGradient>
  </defs>
</svg>

<div class="band" style="top:372px;height:62px"></div>
<div class="band" style="top:776px;height:62px"></div>
<div class="band" style="top:1180px;height:20px"></div>

<!-- Spread: index + about -->
<section class="spread" style="left:42px;top:35px">
  <div class="page left">
    <svg class="bg" viewBox="0 0 259 334">
      <g role="img" aria-label="Photo of a power plant at dusk">
        <polygon points="0,0 30,0 100,150 40,265 40,334 0,334" fill="url(#g-plant)"/>
        <polygon points="0,0 30,0 100,150 40,265 40,334 0,334" fill="url(#g-glow2)"/>
      </g>
      <polyline points="42,-4 110,150 50,265 50,338" fill="none" stroke="var(--yellow)" stroke-width="8"/>
      <polyline points="60,-4 128,150 66,270" fill="none" stroke="var(--ink)" stroke-width="6"/>
      <g role="img" aria-label="Diamond-cropped photos of industrial plants">
        <rect x="148" y="207" width="30" height="30" fill="url(#g-plant)" transform="rotate(45 163 222)"/>
        <rect x="190" y="237" width="30" height="30" fill="url(#g-steel)" transform="rotate(45 205 252)"/>
        <rect x="138" y="268" width="28" height="28" fill="url(#g-sky)" transform="rotate(45 152 282)"/>
        <rect x="196" y="272" width="28" height="28" fill="url(#g-plant)" transform="rotate(45 210 286)"/>
        <rect x="124" y="240" width="9" height="9" fill="var(--yellow)" transform="rotate(45 128 244)"/>
        <rect x="235" y="222" width="7" height="7" fill="var(--navy)" transform="rotate(45 238 225)"/>
      </g>
    </svg>
    <h2 class="index-title abs" style="left:106px;top:28px">INDEX</h2>
    <div class="abs" style="left:106px;top:48px;width:22px;height:2px;background:var(--yellow)"></div>
    <ul class="index-list abs" style="left:146px;top:52px">
      <li>ABOUT OUR COMPANY<span class="dots"></span><span class="num">03</span></li>
      <li>OUR BRANDS<span class="dots"></span><span class="num">04</span></li>
      <li>OUR STOCK<span class="dots"></span><span class="num">05</span></li>
      <li>OUR PRODUCTS<span class="dots"></span><span class="num">06</span></li>
      <li>DIESEL GENERATORS<span class="dots"></span><span class="num">06</span></li>
      <li class="sub-item">STANDBY GENERATORS</li>
      <li class="sub-item">PRIME GENERATORS</li>
      <li class="sub-item">RENTAL GENERATORS</li>
      <li>AC ALTERNATORS<span class="dots"></span><span class="num">09</span></li>
      <li>ALTERNATOR PARTS<span class="dots"></span><span class="num">10</span></li>
      <li>CONTROLLERS<span class="dots"></span><span class="num">11</span></li>
      <li>TRANSFER SWITCHES<span class="dots"></span><span class="num">12</span></li>
      <li>OUR DISTRIBUTORS<span class="dots"></span><span class="num">13</span></li>
    </ul>
    <div class="page-num">02</div>
  </div>
  <div class="page right">
    <svg class="bg" viewBox="0 0 259 334">
      <g role="img" aria-label="Photo of a refinery at night">
        <polygon points="0,0 259,0 259,70 140,150 140,334 0,334" fill="url(#g-night)"/>
        <polygon points="0,0 259,0 259,70 140,150 140,334 0,334" fill="url(#g-glow)"/>
        <polygon points="0,0 259,0 259,70 140,150 140,334 0,334" fill="url(#g-glow2)"/>
      </g>
      <polygon points="140,150 259,70 259,42 140,126" fill="var(--yellow)"/>
    </svg>
    <p class="kicker abs" style="left:22px;top:19px;font-size:10px">ABOUT</p>
    <h1 class="title abs" style="left:22px;top:31px;font-size:14px">BRIGHTLINE ENERGY</h1>
    <p class="sub abs" style="left:22px;top:60px;width:120px;font-size:5.8px">PARTNER WITH A RELIABLE, INNOVATIVE SINGLE SOURCE OF PREMIUM QUALITY POWER GENERATION PRODUCTS</p>
    <div class="photo ph-panel" style="left:52px;top:101px;width:84px;height:152px" role="img" aria-label="Photo of a generator control panel"></div>
    <div class="tiny abs" style="left:146px;top:132px;width:104px">
      <p>For decades we have supplied generators, alternators, parts and controls to contractors, rental fleets and plant operators across the Americas. We keep deep stock close to major ports so orders move fast, and our specialists stay with each project from quote to startup.</p>
      <p>Every unit is tested before it leaves our yard, and each order ships with full manuals, wiring diagrams and a clear warranty. Our team helps you size, select and service the right equipment for the job.</p>
      <p>For decades we have supplied generators, alternators, parts and controls to contractors, rental fleets and plant operators across the Americas. We keep deep stock close to major ports so orders move fast, and our specialists stay with each project from quote to startup.</p>
      <p>Every unit is tested before it leaves our yard, and each order ships with full manuals, wiring diagrams and a clear warranty. Our team helps you size, select and service the right equipment for the job.</p>
    </div>
    <div class="page-num">03</div>
  </div>
</section>

<!-- Spread: brands + stock -->
<section class="spread" style="left:644px;top:35px">
  <div class="page left">
    <svg class="bg" viewBox="0 0 259 334">
      <rect x="0" y="0" width="259" height="58" fill="url(#g-sky)" role="img" aria-label="Photo of an industrial skyline at sunset"/>
    </svg>
    <h2 class="title rule abs" style="left:18px;top:22px">OUR BRAND</h2>
    <div class="brand-row" style="top:80px">
      <p class="label" style="font-size:5.2px">DIESEL GENERATORS</p>
      <p class="tiny">Short note on this product line, the ranges we carry in stock and why our customers keep choosing it for their projects.</p>
      <div class="brand-names"><span class="brand-name">Ardent<br>Gensets</span><span class="brand-name">Kestrel<br>Vantor</span></div>
    </div>
    <div class="brand-row" style="top:126px">
      <p class="label" style="font-size:5.2px">AC ALTERNATORS</p>
      <p class="tiny">Short note on this product line, the ranges we carry in stock and why our customers keep choosing it for their projects.</p>
      <div class="brand-names"><span class="brand-name">Stanhope<br>Arvik</span><span class="brand-name">Lorand<br>Motors</span></div>
    </div>
    <div class="brand-row" style="top:174px">
      <p class="label" style="font-size:5.2px">ALTERNATOR PARTS</p>
      <p class="tiny">Short note on this product line, the ranges we carry in stock and why our customers keep choosing it for their projects.</p>
      <div class="brand-names"><span class="brand-name">Stanhope<br>Arvik</span><span class="brand-name">Lorand<br>Motors</span></div>
    </div>
    <div class="brand-row" style="top:221px">
      <p class="label" style="font-size:5.2px">CONTROLS</p>
      <p class="tiny">Short note on this product line, the ranges we carry in stock and why our customers keep choosing it for their projects.</p>
      <div class="brand-names"><span class="brand-name">Deltec</span><span class="brand-name">Vantor</span></div>
    </div>
    <div class="brand-row" style="top:267px">
      <p class="label" style="font-size:5.2px">TRANSFER SWITCHES</p>
      <p class="tiny">Short note on this product line, the ranges we carry in stock and why our customers keep choosing it for their projects.</p>
      <div class="brand-names"><span class="brand-name">Ascend<br>Switch</span><span class="brand-name">Meridian<br>Electric</span></div>
    </div>
    <div class="page-num">04</div>
  </div>
  <div class="page right">
    <svg class="bg" viewBox="0 0 259 334">
      <rect x="0" y="0" width="259" height="58" fill="url(#g-sky)" role="img" aria-label="Photo of an industrial skyline at sunset"/>
      <polygon points="190,58 259,18 259,58" fill="var(--yellow)"/>
    </svg>
    <h2 class="title rule abs" style="left:18px;top:22px">OUR STOCK</h2>
    <p class="abs" style="left:18px;top:64px;font:600 6px/1.3 Montserrat,sans-serif;color:var(--navy)">COST, LEAD TIME, LOGISTICS AND<br>MANY CHALLENGES</p>
    <p class="abs" style="left:18px;top:81px;font:400 4.4px/1.3 Montserrat,sans-serif;color:var(--navy)">LUCKILY YOU JUST FOUND BRIGHTLINE ENERGY,<br><span style="color:var(--orange)">A SINGLE SOURCE SOLUTION</span></p>
    <div class="photo ph-office" style="left:18px;top:105px;width:70px;height:66px" role="img" aria-label="Photo of the sales team at their desks"></div>
    <ul class="tiny abs" style="left:94px;top:121px;width:152px">
      <li><b>A+</b> rating with the local business bureau</li>
      <li><b>40+</b> years of combined industry experience in North and South America</li>
      <li><b>100+</b> countries served around the world in every continent</li>
      <li><b>100%</b> of our sales specialists factory trained and certified</li>
      <li><b>2000+</b> orders filled each year</li>
      <li><b>5000+</b> products shipped in the last twelve months</li>
    </ul>
    <p class="label abs" style="left:18px;top:182px;font-size:5.4px;font-weight:700">WE SHARE YOUR URGENCY,</p>
    <p class="abs" style="left:18px;top:189px;font:400 4.4px Montserrat,sans-serif;color:var(--navy)">SO WE BECAME EXCELLENT AT SAME DAY:</p>
    <ul class="tiny abs" style="left:18px;top:199px;width:128px">
      <li><b>20+</b> generator trailers from 3500 to 10400 lbs capacity, in stock</li>
      <li><b>50+</b> fuel tanks from 50 to 1000 gallons, in stock</li>
      <li><b>100+</b> automatic transfer switches from 100 to 2000 amps, in stock</li>
      <li><b>200+</b> diesel generators from 10 to 500 kW, in stock</li>
      <li><b>1000+</b> engine parts, alternator parts, voltage regulators and controls, in stock</li>
    </ul>
    <div class="tiny abs" style="left:18px;top:264px;width:128px">
      <p>Brightline Energy offers one of the largest inventories in the region to meet even the most urgent needs.</p>
      <p>We also carry a wide range of regulators and switches, ready to ship the same day to any country in the world.</p>
    </div>
    <div class="photo ph-warehouse" style="left:158px;top:202px;width:101px;height:84px" role="img" aria-label="Photo of a warehouse worker checking stock"></div>
    <div class="note-box abs" style="left:158px;top:286px;width:101px">we will quote same day and<br>we will ship SAME DAY.</div>
    <div class="page-num">05</div>
  </div>
</section>

<!-- Spread: standby + prime -->
<section class="spread" style="left:42px;top:438px">
  <div class="page left">
    <svg class="bg" viewBox="0 0 259 334">
      <g role="img" aria-label="Photo of a plant at night">
        <polygon points="0,0 259,0 259,120 0,205" fill="url(#g-night)"/>
        <polygon points="0,0 259,0 259,120 0,205" fill="url(#g-glow2)"/>
      </g>
      <polygon points="110,169 259,120 259,150" fill="var(--yellow)"/>
    </svg>
    <p class="kicker abs" style="left:18px;top:26px">OUR PRODUCT</p>
    <h2 class="title abs" style="left:18px;top:38px">DIESEL GENERATORS</h2>
    <p class="sub abs" style="left:18px;top:70px">STANDBY<br>GENERATORS</p>
    <div class="photo ph-genset" style="left:96px;top:78px;width:134px;height:86px" role="img" aria-label="Photo of a 100 kW enclosed diesel generator"><span class="genset-kw">100 KW</span></div>
    <p class="label abs" style="left:122px;top:184px">FEATURES</p>
    <ul class="tiny abs" style="left:128px;top:195px;width:122px">
      <li>30 to 500 kW sets powered by tier rated diesel engines, EPA Tier 2, Tier 3 and Tier 4</li>
      <li>13 to 60 kW sets powered by compact diesel engines, EPA Tier 4</li>
      <li>Brushless alternators with optional winding and insulation upgrades</li>
      <li>Digital controllers for stand-alone operation and paralleling (optional)</li>
      <li>12-gauge steel enclosures with stainless steel hardware</li>
      <li>12-gauge aluminum enclosures with stainless steel hardware (optional)</li>
      <li>Critical grade silencers for low noise sites</li>
      <li>Manual main line circuit breakers</li>
      <li>Manual and motorized main line circuit breakers (optional)</li>
      <li>50 to 5000 gallon single-wall fuel tanks</li>
      <li>50 to 5000 gallon double-walled listed fuel tanks</li>
      <li>Battery disconnect switch</li>
      <li>12V starting battery</li>
    </ul>
    <div class="baseline"></div>
    <div class="page-num">06</div>
  </div>
  <div class="page right">
    <svg class="bg" viewBox="0 0 259 334">
      <g role="img" aria-label="Photo of a plant at night">
        <polygon points="0,0 259,0 259,120 0,205" fill="url(#g-night)"/>
        <polygon points="0,0 259,0 259,120 0,205" fill="url(#g-glow)"/>
      </g>
      <polygon points="0,170 130,160 0,205" fill="var(--yellow)"/>
    </svg>
    <p class="kicker abs" style="left:18px;top:26px">OUR PRODUCT</p>
    <h2 class="title abs" style="left:18px;top:38px">DIESEL GENERATORS</h2>
    <p class="sub abs" style="left:18px;top:70px">PRIME<br>GENERATORS</p>
    <div class="photo ph-genset" style="left:96px;top:74px;width:134px;height:86px" role="img" aria-label="Photo of a 100 kW enclosed diesel generator"><span class="genset-kw">100 KW</span></div>
    <p class="label abs" style="left:96px;top:182px">FEATURES</p>
    <ul class="tiny abs" style="left:102px;top:193px;width:128px">
      <li>30 to 500 kW sets powered by tier rated diesel engines, EPA Tier 2, Tier 3 and Tier 4</li>
      <li>13 to 60 kW sets powered by compact diesel engines, EPA Tier 4</li>
      <li>Brushless alternators with optional winding and insulation upgrades</li>
      <li>Digital controllers for stand-alone operation and paralleling (optional)</li>
      <li>12-gauge steel enclosures with stainless steel hardware</li>
      <li>12-gauge aluminum enclosures with stainless steel hardware (optional)</li>
      <li>Critical grade silencers for low noise sites</li>
      <li>Manual main line circuit breakers</li>
      <li>Manual and motorized main line circuit breakers (optional)</li>
      <li>50 to 5000 gallon single-wall fuel tanks</li>
      <li>50 to 5000 gallon double-walled listed fuel tanks</li>
      <li>Battery disconnect switch</li>
      <li>12V starting battery</li>
    </ul>
    <div class="baseline"></div>
    <div class="page-num">07</div>
  </div>
  <svg class="chevron" viewBox="0 0 518 334" aria-hidden="true">
    <polyline points="198,338 274,290 350,338" fill="none" stroke="var(--yellow)" stroke-width="7"/>
    <polyline points="232,338 274,312 316,338" fill="none" stroke="var(--ink)" stroke-width="3"/>
  </svg>
</section>

<!-- Spread: rental + AC alternators -->
<section class="spread" style="left:644px;top:438px">
  <div class="page left">
    <svg class="bg" viewBox="0 0 259 334">
      <g role="img" aria-label="Photo of a refinery lit at night">
        <polygon points="0,0 259,0 259,150 120,185 120,334 0,334" fill="url(#g-night)"/>
        <polygon points="0,0 259,0 259,150 120,185 120,334 0,334" fill="url(#g-glow2)"/>
      </g>
      <polygon points="0,150 120,105 120,185" fill="var(--yellow)" opacity=".85"/>
    </svg>
    <p class="kicker abs" style="left:18px;top:26px">OUR PRODUCT</p>
    <h2 class="title abs" style="left:18px;top:38px">DIESEL GENERATORS</h2>
    <p class="sub abs" style="left:18px;top:70px">RENTAL<br>GENERATORS</p>
    <div class="photo ph-genset" style="left:100px;top:78px;width:134px;height:86px" role="img" aria-label="Photo of a 100 kW enclosed diesel generator"><span class="genset-kw">100 KW</span></div>
    <p class="label abs" style="left:122px;top:184px">FEATURES</p>
    <ul class="tiny abs" style="left:128px;top:195px;width:124px">
      <li>30 to 500 kW sets powered by tier rated diesel engines, EPA Tier 2, Tier 3 and Tier 4</li>
      <li>13 to 60 kW sets powered by compact diesel engines, EPA Tier 4</li>
      <li>Brushless alternators with optional winding and insulation upgrades</li>
      <li>Digital controllers for stand-alone operation and paralleling (optional)</li>
      <li>12-gauge steel enclosures with stainless steel hardware</li>
      <li>12-gauge aluminum enclosures with stainless steel hardware (optional)</li>
      <li>Critical grade silencers for low noise sites</li>
      <li>Manual main line circuit breakers</li>
      <li>Manual and motorized main line circuit breakers (optional)</li>
      <li>50 to 5000 gallon single-wall fuel tanks</li>
      <li>50 to 5000 gallon double-walled listed fuel tanks</li>
      <li>Battery disconnect switch</li>
      <li>12V starting battery</li>
    </ul>
    <div class="baseline"></div>
    <div class="page-num">08</div>
  </div>
  <div class="page right">
    <svg class="bg" viewBox="0 0 259 334">
      <g role="img" aria-label="Photo of an industrial site">
        <polygon points="0,0 259,0 259,75 0,150" fill="url(#g-night)"/>
        <polygon points="0,0 259,0 259,75 0,150" fill="url(#g-glow2)"/>
      </g>
      <polygon points="160,104 259,75 259,50" fill="var(--yellow)"/>
    </svg>
    <p class="kicker abs" style="left:18px;top:26px">OUR PRODUCT</p>
    <h2 class="title abs" style="left:18px;top:38px">AC ALTERNATORS</h2>
    <div class="photo ph-machine" style="left:27px;top:91px;width:66px;height:48px" role="img" aria-label="Photo of a compact AC alternator"></div>
    <div class="photo ph-machine" style="left:118px;top:79px;width:119px;height:108px" role="img" aria-label="Photo of a large AC alternator"></div>
    <p class="label abs" style="left:26px;top:157px">DESCRIPTION</p>
    <div class="tiny abs" style="left:26px;top:168px;width:86px">
      <p>Every unit is tested before it leaves our yard, and each order ships with full manuals, wiring diagrams and a clear warranty. Our team helps you size, select and service the right equipment for the job.</p>
      <p>For decades we have supplied generators, alternators, parts and controls to contractors, rental fleets and plant operators across the Americas.</p>
    </div>
    <p class="tiny abs" style="left:130px;top:203px;width:112px">Every unit is tested before it leaves our yard, and each order ships with full manuals, wiring diagrams and a clear warranty. Our team helps you size, select and service the right equipment for the job.</p>
    <p class="tiny abs" style="left:52px;top:272px;width:190px">For decades we have supplied generators, alternators, parts and controls to contractors, rental fleets and plant operators across the Americas. We keep deep stock close to major ports so orders move fast, and our specialists stay with each project from quote to startup. Every unit is tested before it leaves our yard.</p>
    <div class="baseline"></div>
    <div class="page-num">09</div>
  </div>
  <svg class="chevron" viewBox="0 0 518 334" aria-hidden="true">
    <polyline points="228,338 304,290 380,338" fill="none" stroke="var(--yellow)" stroke-width="7"/>
    <polyline points="262,338 304,312 346,338" fill="none" stroke="var(--ink)" stroke-width="3"/>
  </svg>
</section>

<!-- Spread: alternator parts + controllers -->
<section class="spread" style="left:42px;top:842px">
  <div class="page left">
    <svg class="bg" viewBox="0 0 259 334">
      <g role="img" aria-label="Photo of machined gears">
        <polygon points="0,0 259,0 259,88 0,100" fill="url(#g-steel)"/>
        <polygon points="0,0 259,0 259,88 0,100" fill="url(#g-glow2)"/>
      </g>
    </svg>
    <p class="kicker abs" style="left:18px;top:26px">OUR PRODUCT</p>
    <h2 class="title abs" style="left:18px;top:38px">ALTERNATOR PARTS</h2>
    <div class="photo ph-board" style="left:62px;top:68px;width:66px;height:58px" role="img" aria-label="Photo of a voltage regulator board"></div>
    <div class="photo ph-module" style="left:161px;top:68px;width:70px;height:62px" role="img" aria-label="Photo of an alternator control module"></div>
    <p class="pname abs" style="left:18px;top:136px">PRODUCT<br>NAME</p>
    <p class="pname abs" style="left:166px;top:136px">PRODUCT<br>NAME</p>
    <div class="tiny abs" style="left:18px;top:166px;width:96px">
      <p>Every unit is tested before it leaves our yard, and each order ships with full manuals, wiring diagrams and a clear warranty. Our team helps you size, select and service the right equipment for the job.</p>
      <p>For decades we have supplied generators, alternators, parts and controls to contractors, rental fleets and plant operators across the Americas. We keep deep stock close to major ports so orders move fast.</p>
    </div>
    <div class="tiny abs" style="left:166px;top:166px;width:80px">
      <p>Every unit is tested before it leaves our yard, and each order ships with full manuals, wiring diagrams and a clear warranty. Our team helps you size, select and service the right equipment for the job.</p>
      <p>For decades we have supplied generators, alternators, parts and controls to contractors, rental fleets and plant operators across the Americas. We keep deep stock close to major ports so orders move fast.</p>
    </div>
    <div class="baseline"></div>
    <div class="page-num">10</div>
  </div>
  <div class="page right">
    <svg class="bg" viewBox="0 0 259 334">
      <g role="img" aria-label="Photo of a refinery at night">
        <polygon points="0,0 259,0 259,122 0,152" fill="url(#g-night)"/>
        <polygon points="0,0 259,0 259,122 0,152" fill="url(#g-glow)"/>
      </g>
      <polygon points="140,136 259,122 259,96" fill="var(--yellow)"/>
    </svg>
    <p class="kicker abs" style="left:18px;top:26px">OUR PRODUCT</p>
    <h2 class="title abs" style="left:18px;top:38px">CONTROLLERS</h2>
    <div class="photo ph-controller" style="left:126px;top:78px;width:108px;height:80px" role="img" aria-label="Photo of a digital generator controller"></div>
    <p class="label abs" style="left:20px;top:174px">DESCRIPTION</p>
    <div class="tiny abs" style="left:20px;top:185px;width:94px">
      <p>Every unit is tested before it leaves our yard, and each order ships with full manuals, wiring diagrams and a clear warranty. Our team helps you size, select and service the right equipment for the job.</p>
      <p>For decades we have supplied generators, alternators, parts and controls to contractors, rental fleets and plant operators across the Americas. We keep deep stock close to major ports so orders move fast.</p>
    </div>
    <p class="tiny abs" style="left:128px;top:200px;width:114px">Every unit is tested before it leaves our yard, and each order ships with full manuals, wiring diagrams and a clear warranty. Our team helps you size, select and service the right equipment for the job.</p>
    <p class="tiny abs" style="left:128px;top:258px;width:114px">For decades we have supplied generators, alternators, parts and controls to contractors, rental fleets and plant operators across the Americas. We keep deep stock close to major ports so orders move fast, and our specialists stay with each project from quote to startup.</p>
    <div class="baseline"></div>
    <div class="page-num">11</div>
  </div>
  <svg class="chevron" viewBox="0 0 518 334" aria-hidden="true">
    <polyline points="201,338 277,290 353,338" fill="none" stroke="var(--yellow)" stroke-width="7"/>
    <polyline points="235,338 277,312 319,338" fill="none" stroke="var(--ink)" stroke-width="3"/>
  </svg>
</section>

<!-- Spread: transfer switches + distributors -->
<section class="spread" style="left:644px;top:842px">
  <div class="page left">
    <svg class="bg" viewBox="0 0 259 334">
      <g role="img" aria-label="Photo of an industrial plant">
        <polygon points="0,0 259,0 259,74 170,100 0,100" fill="url(#g-sky)"/>
        <polygon points="0,0 259,0 259,74 170,100 0,100" fill="url(#g-glow2)"/>
      </g>
    </svg>
    <p class="kicker abs" style="left:18px;top:26px">OUR PRODUCT</p>
    <h2 class="title abs" style="left:18px;top:38px">TRANSFER SWITCHES</h2>
    <div class="photo ph-cabinet" style="left:22px;top:82px;width:58px;height:168px" role="img" aria-label="Photo of an automatic transfer switch cabinet"></div>
    <p class="label abs" style="left:120px;top:86px">FEATURES</p>
    <p class="tiny abs" style="left:120px;top:98px;width:100px">Every unit is tested before it leaves our yard, and each order ships with full manuals, wiring diagrams and a clear warranty. Our team helps you size, select and service the right equipment for the job.</p>
    <ul class="tiny abs" style="left:120px;top:150px;width:100px">
      <li>Open and closed transition models</li>
      <li>Service entrance rated options</li>
      <li>Built-in exerciser and adjustable timers</li>
      <li>Digital display with event log</li>
      <li>NEMA rated steel cabinets</li>
      <li>Remote monitoring ready</li>
      <li>Ratings from 100 to 2000 amps</li>
      <li>Bypass isolation models available</li>
      <li>Load shed and priority control</li>
      <li>Front access for service</li>
      <li>Single and three phase units</li>
      <li>Same day shipping from stock</li>
    </ul>
    <p class="tiny abs" style="left:20px;top:258px;width:88px">Short note on this product line, the ranges we carry in stock and why our customers keep choosing it for their projects.</p>
    <div class="baseline"></div>
    <div class="page-num">08</div>
  </div>
  <div class="page right">
    <svg class="bg" viewBox="0 0 259 334">
      <g role="img" aria-label="Photo of an industrial skyline">
        <polygon points="0,0 259,0 259,64 0,64" fill="url(#g-night)"/>
        <polygon points="0,0 259,0 259,64 0,64" fill="url(#g-glow)"/>
      </g>
      <polygon points="190,64 259,24 259,64" fill="var(--yellow)"/>
    </svg>
    <h2 class="title abs" style="left:18px;top:22px">OUR DISTRIBUTORS</h2>
    <div class="dist-strip abs" style="left:16px;top:50px;width:228px;height:28px">
      <span>Ardent</span><span>Kestrel</span><span>Lorand</span><span>Stanhope</span><span>Meridian</span><span>Deltec</span><span>Ascend</span>
    </div>
    <ul class="tiny spaced abs" style="left:20px;top:106px;width:98px">
      <li>Buy direct from the official master distributor for the Americas</li>
      <li>Buy direct from the official parts distributor for the Americas</li>
      <li>Direct access to the largest local stock of alternators and parts</li>
      <li>One hour response time for quotes during business hours</li>
      <li>Online library with datasheets, manuals, diagrams and videos</li>
      <li>Online accounts with pricing, order status and order history</li>
    </ul>
    <ul class="tiny spaced abs" style="left:130px;top:106px;width:112px">
      <li>30 minute response time for pricing and availability requests</li>
      <li>Standard same day shipping on all stock orders placed by 4 pm</li>
      <li>Extended same day shipping on stock orders placed by 6 pm</li>
      <li>Worldwide drop shipping and blind shipping available</li>
      <li>Customer referral program for selected and qualified accounts</li>
      <li>Online training and certification program</li>
    </ul>
    <div class="baseline"></div>
    <div class="page-num">09</div>
  </div>
  <svg class="chevron" viewBox="0 0 518 334" aria-hidden="true">
    <polyline points="186,338 262,290 338,338" fill="none" stroke="var(--yellow)" stroke-width="7"/>
    <polyline points="220,338 262,312 304,338" fill="none" stroke="var(--ink)" stroke-width="3"/>
  </svg>
</section>

</body>
</html>
```